Brightmill Data Works

Our company is about IT hardwares and IT solutions. IT hardware such as PC, RAMS, storage and servers. IT solutions such as project management, BA. We are also selling new technology too.

Target Market(s)

Consumer, Small to Medium Business, Corporate

Requirements
Must have
• The business card must have the following:
• Name:
• Title:
• Contact Number:
• Email address:
• Website:
• Color: Must match the logo color upgrade

```html
<!DOCTYPE html>
<html lang="en">
<head>
<meta charset="utf-8">
<title>Brightmill Data Works – Business Card</title>
<link rel="stylesheet" href="https://fonts.googleapis.com/css2?family=Titillium+Web:wght@400;600;700&family=Roboto+Condensed:wght@400;500&family=Open+Sans:wght@400;600&display=swap">
<style>
  :root {
    --orange: #d9822b;
    --orange-deep: #c4661f;
    --charcoal: #444446;
    --charcoal-dark: #38383a;
    --paper: #f7f7f7;
    --rule: #b8b8b8;
    --text-grey: #555558;
    --stage: #e9e6e1;
  }
  * { box-sizing: border-box; margin: 0; padding: 0; }
  html, body { width: 1200px; height: 950px; overflow: hidden; }
  body { background: var(--stage); position: relative; font-family: "Open Sans", sans-serif; }

  .card {
    position: absolute;
    width: 640px;
    height: 370px;
    border-radius: 4px;
    overflow: hidden;
    box-shadow: 0 10px 26px rgba(0,0,0,.22);
  }

  /* Front */
  .card-front { left: 70px; top: 100px; background: var(--paper); }

  .brand {
    position: absolute;
    right: 70px;
    top: 58px;
    display: flex;
    align-items: center;
    gap: 14px;
  }
  .brand-mark { width: 22px; height: 22px; background: var(--orange); }
  .brand-name {
    font-family: "Titillium Web", sans-serif;
    font-weight: 700;
    font-size: 30px;
    color: var(--charcoal);
    text-transform: uppercase;
    letter-spacing: .5px;
  }

  .divider {
    position: absolute;
    left: 40px; right: 40px;
    top: 140px;
    height: 1px;
    background: var(--rule);
  }

  .person { position: absolute; left: 42px; top: 182px; }
  .person-name {
    font-family: "Roboto Condensed", sans-serif;
    font-size: 27px;
    color: var(--text-grey);
    text-transform: uppercase;
    letter-spacing: .5px;
    line-height: 1.05;
  }
  .person-title {
    font-family: "Roboto Condensed", sans-serif;
    font-size: 15px;
    color: var(--orange);
    text-transform: uppercase;
    margin-top: 2px;
  }
  .person-rule { width: 150px; height: 1px; background: var(--rule); margin: 12px 0 10px; }
  .contact { font-size: 13px; color: var(--text-grey); line-height: 1.6; }

  .front-band { position: absolute; left: 0; bottom: 0; width: 640px; height: 64px; }
  .band-web {
    position: absolute;
    right: 26px;
    bottom: 14px;
    font-weight: 600;
    font-size: 14px;
    color: #fff;
    letter-spacing: .4px;
  }

  /* Back */
  .card-back {
    left: 490px; top: 510px;
    background: var(--charcoal);
  }
  .back-name {
    position: absolute;
    left: 0; right: 0; top: 120px;
    text-align: center;
    font-family: "Titillium Web", sans-serif;
    font-weight: 700;
    font-size: 40px;
    color: var(--orange);
    text-transform: uppercase;
    letter-spacing: 1px;
  }
  .back-web {
    position: absolute;
    right: 40px; bottom: 34px;
    font-weight: 600;
    font-size: 15px;
    color: #f2f2f2;
    letter-spacing: 3px;
  }
</style>
</head>
<body>

  <section class="card card-front" aria-label="Business card front">
    <div class="brand">
      <span class="brand-mark"></span>
      <span class="brand-name">Brightmill Data Works</span>
    </div>

    <div class="divider"></div>

    <div class="person">
      <p class="person-name">Daniel Reyes</p>
      <p class="person-title">CEO/Founder</p>
      <div class="person-rule"></div>
      <p class="contact">555 014 2290<br>daniel@brightmilldata.com</p>
    </div>

    <svg class="front-band" viewBox="0 0 640 64" aria-hidden="true">
      <path d="M0 44 H350 Q360 44 364 36 L372 16 Q376 8 386 8 H640 V64 H0 Z" fill="var(--charcoal)"/>
      <path d="M0 50 H356 Q366 50 370 42 L378 22 Q382 14 392 14 H640 V64 H0 Z" fill="var(--orange)"/>
    </svg>
    <span class="band-web">www.brightmilldata.com</span>
  </section>

  <section class="card card-back" aria-label="Business card back">
    <p class="back-name">Brightmill Data Works</p>
    <p class="back-web">www.brightmilldata.com</p>
  </section>

</body>
</html>
```